Popup Nightclub Grand Opening Flyer

We need to design a flyer for the grand opening of an upscale, exclusive nightclub called "Lantern". The design needs to be chic and exclusive. The background should be black and the text should primarily be white. We like minimalist designs.

Here is the text for the flyer
-
Velvetroll Atlanta Presents

Lantern (LOGO)

A Popup Nightclub Experience
For one night Only

Friday, October 18, 2013
Party begins at 9PM

INVITE ONLY

See invitation for location details
(Velvetroll Atlanta logo)

-
Examples we like

http://cdn4-x.pressfolio-example.com/sites/default/files/styles/image_content_width/hash/3b/fd/2468013579_4421_flyer.jpg?itok=K9rtQw2z

http://files.hubspace-example.net/files/8Hqq-Tr72WWE3kaRbTmcxP5QZK2F396J8nbRw4CKMHfdX2Y7qSEF-MqjxDoNrLY3QCyQJD7npjGaRq3k-Mhx6hqf3MDSWf8r3/2zenSaturdays.jpg

http://morvex-example.com/wp-content/uploads/siteskin/widgetkit/gallery/2zen/2zen-gen_qstay4-01.jpg

Hi All, one thing that we are seeing that we don't like is on over emphasis on the phrase "a popup nightclub experience" please don't make this the largest thing on the flyer

Target Market(s)

Target market is 25-35 year olds who are affluent (rich) and like luxury brands

Requirements
Must have
• Dark Background
Nice to have
• Velvetroll Logo on the bottom
Modern text that isn't curvy
Should not have
• Curved text

```html
<!DOCTYPE html>
<html lang="en">
<head>
<meta charset="utf-8">
<title>Lantern Nightclub – Popup Flyer</title>
<link rel="stylesheet" href="https://fonts.googleapis.com/css2?family=Arimo:wght@400;700&family=Josefin+Sans:wght@300&display=swap">
<style>
  :root {
    --bg-black: #050204;
    --bg-glow: #5c0c3e;
    --bg-mid: #2a0620;
    --headline: #ecd3df;
    --headline-shadow: #9c2c64;
    --text-soft: #d9d2d6;
    --text-white: #ffffff;
    --text-grey: #cfcfcf;
    --brand-silver: #e9e9ee;
    --accent-pink: #ff7fc8;
  }
  * { margin: 0; padding: 0; box-sizing: border-box; }
  html, body { width: 1200px; height: 849px; overflow: hidden; background: var(--bg-black); }
  .flyer {
    position: relative;
    width: 1200px;
    height: 849px;
    overflow: hidden;
    font-family: "Arimo", Arial, sans-serif;
    background:
      radial-gradient(ellipse 620px 420px at 600px 440px, var(--bg-glow) 0%, var(--bg-mid) 55%, transparent 100%),
      var(--bg-black);
  }
  .event-info {
    position: absolute;
    top: 24px;
    font-weight: 700;
    font-size: 30px;
    line-height: 40px;
    color: var(--headline);
    text-align: center;
    text-shadow: 2px 2px 0 var(--headline-shadow);
  }
  .event-date { left: 60px; width: 300px; }
  .event-time { left: 498px; width: 300px; }
  .event-access { left: 886px; width: 300px; }

  .presenter {
    position: absolute;
    top: 203px;
    left: 0;
    width: 1200px;
    text-align: center;
    font-weight: 700;
    font-size: 20px;
    color: var(--text-grey);
  }
  .club-mark {
    position: absolute;
    top: 252px;
    left: 0;
    width: 1200px;
    display: flex;
    flex-direction: column;
    align-items: center;
    font-family: "Josefin Sans", Arial, sans-serif;
    font-weight: 300;
    color: var(--brand-silver);
  }
  .club-mark-dot {
    width: 110px;
    height: 110px;
    border-radius: 50%;
    border: 3px solid var(--brand-silver);
    margin-bottom: 80px;
  }
  .club-name {
    font-size: 60px;
    letter-spacing: 10px;
    line-height: 60px;
    padding-left: 10px;
  }
  .club-type {
    margin-top: 12px;
    font-size: 30px;
    letter-spacing: 6px;
    line-height: 30px;
    padding-left: 6px;
  }
  .tagline {
    position: absolute;
    top: 600px;
    font-weight: 700;
    font-size: 21px;
    letter-spacing: 4.6px;
    color: var(--text-soft);
  }
  .tagline-left { left: 47px; }
  .tagline-right { left: 770px; }

  .location-note {
    position: absolute;
    top: 684px;
    left: 0;
    width: 1310px;
    text-align: center;
    font-weight: 700;
    font-size: 22px;
    color: var(--text-white);
  }
  .host-mark {
    position: absolute;
    top: 730px;
    left: 442px;
    width: 410px;
    height: 76px;
    display: flex;
    align-items: center;
    justify-content: center;
    gap: 16px;
    color: var(--text-white);
    font-weight: 700;
    font-size: 30px;
    letter-spacing: 4px;
  }
  .host-mark-square {
    width: 26px;
    height: 26px;
    background: var(--accent-pink);
  }
</style>
</head>
<body>
  <main class="flyer">
    <p class="event-info event-date">Friday,<br>October 18, 2013</p>
    <p class="event-info event-time">Party begins<br>at 9PM</p>
    <p class="event-info event-access">INVITE ONLY</p>

    <p class="presenter">Velvetroll Atlanta Presents</p>

    <div class="club-mark">
      <span class="club-mark-dot" aria-hidden="true"></span>
      <span class="club-name">LANTERN</span>
      <span class="club-type">NIGHTCLUB</span>
    </div>

    <p class="tagline tagline-left">A Popup Nightclub Experience</p>
    <p class="tagline tagline-right">For one night Only</p>

    <p class="location-note">See invitation for location details</p>

    <div class="host-mark">
      <span class="host-mark-square" aria-hidden="true"></span>
      <span class="host-mark-name">VELVETROLL ATLANTA</span>
    </div>
  </main>
</body>
</html>
```